Home page design for Drone video business (the Business focusses on home videos for realtors)

Dear reader,

*I NEED DESIGNS OF ALL THE PAGES*
We need a first design of a homepage and of 4 other pages of the website of a business that sells drone video services. All the pages will need to be in the similar design style.
The video's are targeted at consumers that want to sell there home and would like to have a cool drone video of photos of their home.

How does the website look:
- has a navbar on top
- A cool looking banner of an areal drone.
- A Big header: with company name: SkyLoftReels
- A smaller subheader: We film your home to increase your chances of sale
- Then a section with a Big header: How does it work
- In this section a place for a vimeo explainitory video
- Then a similar navbar styled bar with a phone number and a email address
- Then a section where the videos porfolio is displayed in a cool way
- Inside this sectiona header: Our work

- A section with header: Why us?
- 4 symbols here with a subheader and some lorum ipsum text underneath (see wireframe images)

- Under that a: Contact us
- where you can put in name, email, phone, message box and a send button

- At the bottom a footer with phone number and a fake address for now.

Be creative. Use creative but serious color.
Use a serious font. Make it a sharp design. Sharp lines. Not to dark design and not to light design.

The wireframes are the same kind of images.
PLEASE PUT IN DESIGNS OF ALL THE PAGES

Good luck

Target Market(s)

People that want to sell home and want to make a cool drone video or photos of their home.

Industry/Entity Type

Business

Contact Information for Business Card

Lucas Wenning
lucas@skyloftreels.example
+31647208351

Logo Text

SkyLoftReels

Number of Pages Required

1 page

Font styles to use
Sans Serif

Requirements
Must have
• All the sections as explained in the instructions.
• The nav bar should have an about us, services, portfolio and a contact us buttons.
• See instruction for details.
• Must include designs of the front page, contact us, our services, portfolio and contact us.
• If you do add some designs for the "about us", "services", "prices", "portfolio" and "contact us" pages, you make a way better chance of winning the competition.
Nice to have
• designs for the other pages as described at the Must haves. You make a better chance of winning if you include them. Look at the wireframes to see the mockups for those pages. think creative about what kind of sections and design should be included in those pages.
Should not have
• bad designs.

```html
<!DOCTYPE html>
<html lang="en">
<head>
<meta charset="utf-8">
<title>SkyLoftReels – Home</title>
<link rel="stylesheet" href="https://fonts.googleapis.com/css2?family=Lato:wght@400;700;900&family=Montserrat:wght@500;600;700&display=swap">
<style>
:root{
  --accent:#b95da7;
  --ink:#111111;
  --text:#333333;
  --muted:#555555;
  --white:#ffffff;
  --soft:#f4f4f4;
  --line:#cfcfcf;
  --footer:#222222;
  --sky-top:#6f97d8;
  --sky-bottom:#b9cde8;
  --roof:#b4633e;
}
*{box-sizing:border-box;margin:0;padding:0}
html,body{width:1200px;height:2525px;overflow:hidden;background:var(--white)}
body{position:relative;font-family:"Lato",sans-serif;color:var(--text)}
.abs{position:absolute}

/* nav */
.site-nav{left:0;top:0;width:1200px;height:81px;background:var(--white)}
.brand{left:96px;top:18px;font-family:"Lato",sans-serif;font-weight:900;font-size:40px;color:var(--accent);line-height:44px}
.nav-link{top:27px;height:39px;line-height:39px;font-size:16px;color:var(--ink)}
.nav-link.is-active{background:var(--accent);color:var(--white);width:86px;text-align:center;left:444px}

/* hero */
.hero{left:0;top:81px;width:1200px;height:471px;background:linear-gradient(180deg,var(--sky-top) 0%,var(--sky-bottom) 45%,#c99a78 62%,var(--roof) 78%,#d9c3a6 100%)}
.hero-title{left:560px;width:550px;text-align:center;top:112px;font-family:"Lato",sans-serif;font-weight:900;font-size:33px;letter-spacing:1px;color:var(--ink)}
.hero-sub{left:560px;width:550px;text-align:center;top:166px;font-size:29px;line-height:36px;color:var(--ink)}
.slide-btn{width:24px;height:24px;background:#3a3a3a;display:flex;align-items:center;justify-content:center}
.slide-btn.purple{background:var(--accent)}

/* how */
.how-media{left:116px;top:602px;width:517px;height:411px;border:2px solid var(--line);background:linear-gradient(180deg,#c9d6e8 0%,#a4a39e 45%,#6d6a63 70%,#e8ecef 100%)}
.play{width:84px;height:84px;border-radius:50%;background:var(--white);display:flex;align-items:center;justify-content:center}
.play.small{width:68px;height:68px;background:rgba(255,255,255,.9)}
.how-card{left:584px;top:668px;width:502px;height:317px;background:#f2f2f2;box-shadow:0 1px 4px rgba(0,0,0,.18)}
.section-title{font-family:"Montserrat",sans-serif;font-weight:600;color:var(--ink)}
.section-title em{font-style:normal;color:var(--accent)}
.how-card .section-title{position:absolute;left:35px;top:22px;font-size:36px}
.how-rule{position:absolute;left:205px;top:99px;width:92px;height:2px;background:var(--accent)}
.how-copy{position:absolute;left:35px;top:125px;width:440px;font-size:13px;line-height:24px;color:var(--muted)}
.tick-list{position:absolute;left:35px;top:200px;list-style:none}
.tick-list li{display:flex;align-items:center;gap:12px;height:26px;font-size:12.5px;color:var(--muted)}

.contact-pill{top:1054px;height:55px;border:1px solid #b9b9b9;background:#efefef;display:flex;align-items:center;gap:10px;padding-left:20px;font-family:"Lato",sans-serif;font-weight:700;font-size:19px;color:var(--ink)}
.pill-icon{width:36px;height:36px;border-radius:50%;border:2px solid var(--accent);display:flex;align-items:center;justify-content:center}

/* sections */
.band{left:0;width:1200px;background:var(--soft)}
.center-title{left:0;width:1200px;text-align:center;font-size:36px}
.divider{left:382px;width:436px;height:1px;background:var(--line)}
.divider::after{content:"";position:absolute;left:168px;top:-1px;width:100px;height:3px;background:var(--accent)}

.work-thumb{top:1281px;width:284px;height:286px;border-radius:6px;display:flex;align-items:center;justify-content:center}
.thumb-a{left:150px;background:linear-gradient(180deg,#3b78d6 0%,#7fa6dc 45%,#7a5a45 70%,#3f4a3a 100%)}
.thumb-b{left:458px;background:linear-gradient(90deg,#5a2f24 0%,#8a4a35 50%,#3a2a24 100%)}
.thumb-c{left:767px;background:linear-gradient(180deg,#d8dde0 0%,#8b9a7c 45%,#2f4a2a 75%,#c9c2bb 100%)}

.feature{top:1745px;width:260px;text-align:center}
.feature-icon{width:108px;height:108px;border-radius:50%;background:var(--accent);margin:0 auto;display:flex;align-items:center;justify-content:center}
.feature h3{margin-top:30px;font-family:"Lato",sans-serif;font-weight:700;font-size:21px;color:var(--ink);letter-spacing:.3px}
.feature p{margin-top:8px;font-size:13px;line-height:20.5px;color:#222}

.field{background:var(--white);border:1px solid #a9a9a9;font-size:12px;color:#222;padding:10px 10px}
.send-btn{left:549px;top:2392px;width:102px;height:38px;background:var(--accent);color:var(--white);font-size:15px;letter-spacing:1.5px;text-align:center;line-height:38px}

.site-footer{left:0;top:2472px;width:1200px;height:53px;background:var(--footer);color:var(--white)}
.footer-item{top:0;height:53px;display:flex;align-items:center;gap:10px;font-size:18px}
.copyright{right:96px;top:0;line-height:53px;font-size:12px;font-weight:700}
</style>
</head>
<body>

<header class="abs site-nav">
  <div class="abs brand">SkyLoftReels</div>
  <div class="abs nav-link is-active">Home</div>
  <div class="abs nav-link" style="left:594px">Services</div>
  <div class="abs nav-link" style="left:725px">About Us</div>
  <div class="abs nav-link" style="left:865px">Portfolio</div>
  <div class="abs nav-link" style="left:1001px">Contact Us</div>
</header>

<section class="abs hero" role="img" aria-label="Drone hovering above terracotta tile roofs against a blue sky"></section>
<h1 class="abs hero-title">SKYLOFTREELS</h1>
<p class="abs hero-sub">We Film Your Home To<br>Increase Your Chances of Sale</p>
<div class="abs slide-btn" style="left:62px;top:293px"><svg width="10" height="14" viewBox="0 0 10 14"><path d="M8 1 2 7l6 6" fill="none" stroke="#fff" stroke-width="1.6"/></svg></div>
<div class="abs slide-btn" style="left:1114px;top:293px"><svg width="10" height="14" viewBox="0 0 10 14"><path d="M2 1l6 6-6 6" fill="none" stroke="#fff" stroke-width="1.6"/></svg></div>

<div class="abs how-media" role="img" aria-label="Explainer video still: drone filming a stone house in snow">
  <div class="abs play" style="left:214px;top:162px"><svg width="26" height="28" viewBox="0 0 26 28"><path d="M5 2v24l19-12z" fill="#111"/></svg></div>
</div>
<div class="abs how-card">
  <h2 class="section-title">How Does <em>It Work?</em></h2>
  <div class="how-rule"></div>
  <p class="how-copy">Lorem ipsum dolor sit amet, consectetuer adipiscing elit, sed diam nonummy nibh euismod tincidunt ut laoreet dolore magna aliquam erat volutpat. Ut wisi enim ad minim veniam, quis nostrud exerci tation</p>
  <ul class="tick-list">
    <li><svg width="18" height="14" viewBox="0 0 18 14"><path d="M2 7l5 5L16 2" fill="none" stroke="#b95da7" stroke-width="3"/></svg>Lorem ullamcorper suscipit lobortis nisl ut aliquip ex ea commodo</li>
    <li><svg width="18" height="14" viewBox="0 0 18 14"><path d="M2 7l5 5L16 2" fill="none" stroke="#b95da7" stroke-width="3"/></svg>Lorem ullamcorper suscipit lobortis nisl ut aliquip ex ea commodo</li>
    <li><svg width="18" height="14" viewBox="0 0 18 14"><path d="M2 7l5 5L16 2" fill="none" stroke="#b95da7" stroke-width="3"/></svg>Lorem ullamcorper suscipit lobortis nisl ut aliquip ex ea commodo</li>
  </ul>
</div>

<div class="abs contact-pill" style="left:342px;width:249px">
  <span class="pill-icon"><svg width="18" height="18" viewBox="0 0 24 24"><path d="M6.6 10.8a15 15 0 0 0 6.6 6.6l2.2-2.2a1 1 0 0 1 1-.25 11.4 11.4 0 0 0 3.6.57 1 1 0 0 1 1 1V20a1 1 0 0 1-1 1A17 17 0 0 1 3 4a1 1 0 0 1 1-1h3.5a1 1 0 0 1 1 1c0 1.25.2 2.45.57 3.6a1 1 0 0 1-.25 1z" fill="#b95da7"/></svg></span>+31662490175
</div>
<div class="abs contact-pill" style="left:608px;width:249px;font-size:16px;gap:8px;padding-left:14px">
  <span class="pill-icon"><svg width="18" height="14" viewBox="0 0 18 14"><rect x="1" y="1" width="16" height="12" fill="#b95da7"/><path d="M1 1l8 7 8-7" fill="none" stroke="#fff" stroke-width="1.4"/></svg></span>contact@skyloftreels.example
</div>

<section class="abs band" style="top:1155px;height:452px"></section>
<h2 class="abs section-title center-title" style="top:1180px">Our <em>Work?</em></h2>
<div class="abs divider" style="top:1249px"></div>
<div class="abs slide-btn purple" style="left:62px;top:1432px;width:26px;height:26px"><svg width="10" height="14" viewBox="0 0 10 14"><path d="M8 1 2 7l6 6" fill="none" stroke="#222" stroke-width="1.6"/></svg></div>
<div class="abs slide-btn purple" style="left:1114px;top:1432px;width:26px;height:26px"><svg width="10" height="14" viewBox="0 0 10 14"><path d="M2 1l6 6-6 6" fill="none" stroke="#222" stroke-width="1.6"/></svg></div>
<div class="abs work-thumb thumb-a" role="img" aria-label="Portfolio video: brick house with drone in blue sky"><div class="play small"><svg width="22" height="24" viewBox="0 0 26 28"><path d="M5 2v24l19-12z" fill="#111"/></svg></div></div>
<div class="abs work-thumb thumb-b" role="img" aria-label="Portfolio video: white drone beside a brick apartment building"><div class="play small"><svg width="22" height="24" viewBox="0 0 26 28"><path d="M5 2v24l19-12z" fill="#111"/></svg></div></div>
<div class="abs work-thumb thumb-c" role="img" aria-label="Portfolio video: drone above a house among trees"><div class="play small"><svg width="22" height="24" viewBox="0 0 26 28"><path d="M5 2v24l19-12z" fill="#111"/></svg></div></div>

<h2 class="abs section-title center-title" style="top:1636px">Why <em>Us?</em></h2>
<div class="abs divider" style="top:1712px"></div>

<div class="abs feature" style="left:92px">
  <div class="feature-icon"><svg width="60" height="50" viewBox="0 0 60 50"><ellipse cx="30" cy="28" rx="22" ry="16" fill="#fff"/><rect x="16" y="38" width="7" height="10" fill="#fff"/><rect x="37" y="38" width="7" height="10" fill="#fff"/><circle cx="30" cy="8" r="6" fill="#fff"/><rect x="50" y="24" width="8" height="8" fill="#fff"/></svg></div>
  <h3>CHEAP</h3>
  <p>Lorem ipsum dolor sit amet,<br>consectetuer sit al adipiscing elit, sed<br>diam nonummy nibh dolor euismod<br>tincidunt ut laoreet dolore</p>
</div>
<div class="abs feature" style="left:331px">
  <div class="feature-icon"><svg width="62" height="62" viewBox="0 0 62 62" fill="none" stroke="#fff" stroke-width="4"><circle cx="14" cy="14" r="9"/><circle cx="48" cy="14" r="9"/><circle cx="14" cy="48" r="9"/><circle cx="48" cy="48" r="9"/><rect x="23" y="23" width="16" height="16"/></svg></div>
  <h3>FLEXIBLE</h3>
  <p>Lorem ipsum dolor sit amet,<br>consectetuer sit al adipiscing elit, sed<br>diam nonummy nibh dolor euismod<br>tincidunt ut laoreet dolore</p>
</div>
<div class="abs feature" style="left:570px">
  <div class="feature-icon"><svg width="64" height="54" viewBox="0 0 64 54"><rect x="3" y="3" width="58" height="48" fill="none" stroke="#fff" stroke-width="4"/><text x="32" y="30" text-anchor="middle" font-family="Lato,sans-serif" font-weight="900" font-size="20" fill="#fff">4K</text><rect x="9" y="35" width="46" height="11" fill="#fff"/><text x="32" y="44" text-anchor="middle" font-family="Lato,sans-serif" font-weight="700" font-size="8" fill="#b95da7">FULLHD</text></svg></div>
  <h3>4K QUALITY</h3>
  <p>Lorem ipsum dolor sit amet,<br>consectetuer sit al adipiscing elit, sed<br>diam nonummy nibh dolor euismod<br>tincidunt ut laoreet dolore</p>
</div>
<div class="abs feature" style="left:834px">
  <div class="feature-icon"><svg width="58" height="58" viewBox="0 0 58 58" fill="#fff" stroke="#b95da7" stroke-width="1.5"><rect x="4" y="28" width="18" height="26" rx="3"/><rect x="20" y="6" width="18" height="48" rx="3"/><rect x="36" y="18" width="18" height="36" rx="3"/></svg></div>
  <h3>INCREASE SALE CHANCE</h3>
  <p>Lorem ipsum dolor sit amet,<br>consectetuer sit al adipiscing elit, sed<br>diam nonummy nibh dolor euismod<br>tincidunt ut laoreet dolore</p>
</div>

<section class="abs band" style="top:2060px;height:412px"></section>
<h2 class="abs section-title center-title" style="top:2094px">Contact <em>Us</em></h2>
<div class="abs divider" style="top:2171px"></div>
<div class="abs field" style="left:151px;top:2223px;width:300px;height:42px">Name</div>
<div class="abs field" style="left:151px;top:2274px;width:300px;height:42px">Email</div>
<div class="abs field" style="left:151px;top:2326px;width:300px;height:42px">Phone</div>
<div class="abs field" style="left:463px;top:2223px;width:586px;height:145px;padding-top:6px">Message</div>
<div class="abs send-btn">SEND</div>

<footer class="abs site-footer">
  <div class="abs footer-item" style="left:96px"><svg width="20" height="22" viewBox="0 0 24 24"><path d="M6.6 10.8a15 15 0 0 0 6.6 6.6l2.2-2.2a1 1 0 0 1 1-.25 11.4 11.4 0 0 0 3.6.57 1 1 0 0 1 1 1V20a1 1 0 0 1-1 1A17 17 0 0 1 3 4a1 1 0 0 1 1-1h3.5a1 1 0 0 1 1 1c0 1.25.2 2.45.57 3.6a1 1 0 0 1-.25 1z" fill="#fff"/></svg>+31662490175</div>
  <div class="abs footer-item" style="left:262px"><svg width="26" height="18" viewBox="0 0 26 18"><rect x="1" y="1" width="24" height="16" fill="#fff"/><path d="M1 1l12 9 12-9" fill="none" stroke="#222" stroke-width="1.6"/></svg>contact@skyloftreels.example</div>
  <div class="abs copyright">COPYRIGHT © 2016 SKYLOFTREELS. ALL RIGHTS RESERVED.</div>
</footer>

</body>
</html>
```